US-based arts and education non-profit needs logo and signage for South African affiliate

We need a logo and sign for the "Scrap to Splendor" (STS) recycling program, based out of a local community center in Port Elizabeth, South Africa. The community center also houses a community garden and afterschool program. The sign should be 5' x 4'. Title: Scrap to Splendor (with logo). Subtitle 1: "Our Shared Lantern". Subtitle 2: "in partnership with Lantern Nine" (with Lantern Nine logo). We would like to see designs that are vibrant and welcoming. The final design should communicate joy and community.

```html
<!DOCTYPE html>
<html lang="en">
<head>
<meta charset="utf-8">
<title>Scrap to Splendor – Our Shared Lantern sign</title>
<link rel="stylesheet" href="https://fonts.googleapis.com/css2?family=Bebas+Neue&family=Montserrat:wght@500;600&family=Nunito:wght@400;600&display=swap">
<style>
  :root {
    --page: #ffffff;
    --sun-light: #f1dca6;
    --sun-deep: #ead081;
    --tab: #ffffff;
    --brand-green: #4f8a3b;
    --head-green: #3b6a2d;
    --head-brown: #5c3d17;
    --ink: #222222;
    --partner: #6a2f96;
    --hill-light: #5a9142;
    --hill-dark: #3c6b2e;
    --figure-warm: #e9b65a;
    --figure-cool: #6a9fd8;
    --figure-pink: #f26a86;
  }
  * { box-sizing: border-box; margin: 0; padding: 0; }
  html, body {
    width: 1200px; height: 1200px; overflow: hidden;
    background: var(--page);
  }
  .sign {
    position: absolute; left: 147px; top: 242px;
    width: 906px; height: 725px; overflow: hidden;
    background: radial-gradient(circle at 50% 78%, var(--sun-light) 0%, var(--sun-light) 35%, var(--sun-deep) 100%);
  }
  .brand-tab {
    position: absolute; left: 0; top: 0; width: 906px; height: 206px;
  }
  .brand-mark {
    position: absolute; left: 413px; top: 36px;
    width: 76px; height: 76px; border-radius: 50%;
    background: var(--brand-green);
  }
  .brand-name {
    position: absolute; left: 0; width: 906px; top: 132px;
    text-align: center;
    font-family: "Nunito", sans-serif; font-weight: 400;
    font-size: 24px; letter-spacing: 0.5px; color: var(--brand-green);
  }
  .brand-tagline {
    position: absolute; left: 0; width: 906px; top: 168px;
    text-align: center;
    font-family: "Nunito", sans-serif; font-weight: 600;
    font-size: 10.5px; letter-spacing: 0.4px; color: var(--brand-green);
  }
  .headline {
    position: absolute; left: 0; width: 906px; top: 236px;
    text-align: center;
    font-family: "Bebas Neue", sans-serif;
    font-size: 142px; line-height: 114px;
  }
  .headline .line-one { display: block; color: var(--head-green); }
  .headline .line-two { display: block; color: var(--head-brown); }
  .partner-lead {
    position: absolute; left: 0; width: 906px; top: 468px;
    text-align: center;
    font-family: "Montserrat", sans-serif; font-weight: 500;
    font-size: 23px; color: var(--ink);
  }
  .partner {
    position: absolute; left: 309px; top: 513px;
    display: flex; align-items: center; gap: 16px;
  }
  .partner-mark {
    width: 72px; height: 72px; border-radius: 50%;
    background: var(--partner);
  }
  .partner-name {
    font-family: "Montserrat", sans-serif; font-weight: 600;
    font-size: 27px; letter-spacing: 1px; color: var(--partner);
  }
  .landscape { position: absolute; left: 0; top: 0; }
  .figure {
    position: absolute; border-radius: 40px;
  }
  .figure-recycler {
    left: 36px; top: 402px; width: 238px; height: 288px;
    background: linear-gradient(160deg, var(--figure-warm), var(--figure-cool));
  }
  .figure-collector {
    left: 695px; top: 402px; width: 160px; height: 294px;
    background: linear-gradient(180deg, var(--figure-pink), #2a4f8e);
  }
</style>
</head>
<body>
  <main class="sign">
    <svg class="landscape" width="906" height="725" viewBox="0 0 906 725" aria-hidden="true">
      <path class="brand-tab-shape" d="M268 0 H638 L620 176 Q616 204 588 204 H318 Q290 204 287 176 Z" fill="var(--tab)"/>
      <path d="M0 610 Q250 580 420 625 L906 625 V725 H0 Z" fill="var(--hill-light)"/>
      <path d="M250 612 Q350 620 440 630 Q560 640 620 600 Q700 585 820 600 Q880 610 906 620 V725 H0 Z" fill="var(--hill-dark)"/>
      <path d="M0 610 Q200 600 290 640 Q420 690 450 725 H0 Z" fill="var(--hill-light)"/>
      <path d="M820 600 Q880 605 906 622 V725 H870 Q850 650 820 600 Z" fill="var(--hill-light)"/>
    </svg>

    <header class="brand-tab">
      <div class="brand-mark"></div>
      <p class="brand-name">SCRAP TO SPLENDOR</p>
      <p class="brand-tagline">Our Shared Lantern</p>
    </header>

    <h1 class="headline">
      <span class="line-one">OUR SHARED</span>
      <span class="line-two">LANTERN</span>
    </h1>

    <p class="partner-lead">In partnership with</p>
    <div class="partner">
      <div class="partner-mark"></div>
      <span class="partner-name">LANTERN NINE</span>
    </div>

    <div class="figure figure-recycler" role="img" aria-label="Illustration of a woman waving while placing a rubbish bag into a blue recycling bin"></div>
    <div class="figure figure-collector" role="img" aria-label="Illustration of a man carrying a cardboard box of recyclable bottles"></div>
  </main>
</body>
</html>
```